Property Portal needs Chatterloop Cover Image and Sponsor Ad Design

WHO WE ARE
Hi Pitchers! We are an advertising portal that focus on presenting the latest property launches in Singapore. Our platform and interface will provide consumer an enjoyable and easy browsing experience looking for their ideal property to buy/invest, while ensuring updated information, images/videos, and other useful description is provided on each project.

WHAT WE NEED
Our website is www.brightkeyhomes.sg, and we need designs for our Chatterloop page www.facebook.com/brightkeyhomes. One as the Cover Image (815 x 315), and one as our Sponsor Ad Image (1200 x 627). The 2 designs can be similar or different.

DESIGN
We want to convey a professional and sociable feel. A "cool" and elegant design may be suitable, although feel free to have your own look & feel as long as it suits our purpose. Try to have a focus, and not look messy. We don't want to look cheap, spammy or boring in any sense. Be creative and purposeful =) You may use the snapvault images attached or you can use your own. Add symbols or graphics if it helps to give the design a better feel.

For your reference, I find there is a number of good designs with nice look & feel in this project including those withdraw/eliminated.
http://chatterloop.pitchmart.example/contest.aspx?id=218907&page=2
http://chatterloop.pitchmart.example/contest.aspx?id=218907

IDEAS
You may want to embed our portal in an SLATEX device as part of the design (see samples below but replace callpod with SlateX). And/or you can have a blur-out image background to have a focus on what you want to show. Please note that we are not restricting any other designs concept, this is just an idea I have.

CAPTIONS
You may use one or a few of the sample captions below.
- Singapore Latest Property Launches In One Portal (slight emphasis on "in one portal")
- Latest Projects • Updated Info • Best Pricing
- Residential • Commercial • Overseas (perhaps label on images)

Hope we can find an ideal design here. We will request from pitchmart to increase the project budget to give out more participation payments if there is a few good ones. We are also looking to find suitable designers for our future projects as we need a few more designs. If you have questions, feel free to ask me and I will reply promptly.

Reason: Project cancelled and relaunch with different purpose, moved from Newsletter to Chatterloop Design.

IDEAS (UPDATED) I am thinking one way to showcase our portal is perhaps to have our website embedded in an slatex and/or notebook pro device as part of the design. I've attached some designs I came across to show what I mean (only the embedding part). If you are going to do it this way, you can use our main page www.brightkeyhomes.sg and/or a project page www.brightkeyhomes.sg/willowcrest-at-ambergate to display

Target Market(s)

Real Estate Agents, Investors, Developers, General public age 30 & above

Industry/Entity Type

Advertising

Colors
9ccb3b
00a98f
0592cd
3176b5
ffcf3e
5c5c5c

Requirements
Should not have
• I prefer not to use real people stock images unless you are very sure it will work out well.

```html
<!DOCTYPE html>
<html lang="en">
<head>
<meta charset="utf-8">
<title>Brightkeyhomes Cover</title>
<link rel="stylesheet" href="https://fonts.googleapis.com/css2?family=Open+Sans:wght@300;400;600;700&display=swap">
<style>
  :root {
    --teal: #00a98f;
    --green: #8dc63f;
    --green-dark: #3f8a2e;
    --white: #ffffff;
    --ink: #5c5c5c;
    --device: #111214;
    --sky: #7fb6dc;
    --sky-pale: #cfe3ef;
    --lawn: #7aa84a;
    --stone: #c9b9a4;
  }
  * { box-sizing: border-box; margin: 0; padding: 0; }
  html, body { width: 1200px; height: 444px; overflow: hidden; background: var(--white); }
  body { font-family: "Open Sans", Arial, sans-serif; }
  .cover { position: relative; width: 1200px; height: 444px; overflow: hidden; background: var(--white); }

  .headline-panel {
    position: absolute; left: 11px; top: 11px; width: 688px; height: 205px;
    background: var(--teal); color: var(--white);
    padding: 42px 0 0 38px;
  }
  .headline { font-weight: 400; font-size: 46px; line-height: 58px; letter-spacing: -0.4px; white-space: nowrap; }
  .headline strong { font-weight: 700; }

  .photo { position: absolute; }
  .photo-residential { left: 11px; top: 230px; width: 339px; height: 203px;
    background: linear-gradient(180deg, var(--sky) 0%, var(--sky-pale) 55%, var(--stone) 70%, var(--lawn) 100%); }
  .photo-commercial { left: 364px; top: 230px; width: 335px; height: 203px;
    background: linear-gradient(180deg, #5d9fd0 0%, #b9d6e8 50%, #d9dde0 68%, #6f9a45 100%); }
  .photo-tower { left: 713px; top: 11px; width: 476px; height: 422px;
    background: linear-gradient(180deg, #e9eef0 0%, #d7dfe2 40%, #8e9a8f 70%, #5f8a3c 100%); }

  .tablet {
    position: absolute; left: 652px; top: 66px; width: 282px; height: 376px;
    background: var(--device); border-radius: 24px; border: 2px solid #3a3c40;
  }
  .screen {
    position: absolute; left: 25px; top: 24px; width: 229px; height: 326px;
    background: var(--white); overflow: hidden; color: var(--ink);
    font-size: 5px; line-height: 1.3;
  }
  .site-header { height: 32px; display: flex; flex-direction: column; align-items: center; padding-top: 5px; }
  .site-brand { font-size: 10px; font-weight: 600; color: var(--green-dark); line-height: 13px; }
  .site-nav { display: flex; gap: 8px; font-size: 4.5px; margin-top: 4px; }
  .site-nav span:first-child { font-weight: 600; color: var(--green-dark); }
  .site-menu { height: 8px; background: var(--teal); border-top: 2px solid var(--green-dark); }
  .site-hero { position: relative; height: 62px;
    background: linear-gradient(180deg, #4c93c9 0%, #a8cde4 60%, #6f9e55 100%); }
  .hero-title { position: absolute; right: 8px; top: 8px; text-align: right; color: var(--white);
    font-size: 8px; font-weight: 600; }
  .hero-title span { display: block; font-size: 4.5px; font-weight: 400; }
  .hero-tagline { position: absolute; left: 8px; bottom: 5px; color: var(--white); font-size: 6px; font-style: italic; }
  .site-body { display: flex; padding: 8px 6px; gap: 6px; }
  .listing { width: 68px; }
  .listing-image { height: 34px; background: linear-gradient(180deg, #8fbbd9, #7aa35a); }
  .listing-title { font-size: 6px; color: var(--green-dark); font-weight: 600; margin: 3px 0 2px; white-space: nowrap; }
  .listing-line { margin-bottom: 1px; }
  .listing-button { display: inline-block; margin-top: 4px; padding: 1px 4px; border: 0.5px solid #bbb; font-size: 4.5px; }
  .sidebar { flex: 1; }
  .sidebar-title { font-size: 6px; font-weight: 600; color: var(--green-dark); margin-bottom: 3px; }
  .field { height: 7px; border: 0.5px solid #ccc; margin: 1px 0 3px; }
  .search-button { width: 26px; padding: 1px 0; text-align: center; color: var(--white); background: var(--teal); margin-bottom: 8px; }

  .brand-badge { position: absolute; left: 866px; top: 311px; width: 334px; height: 108px; }
  .brand-badge svg { position: absolute; inset: 0; }
  .brand-name { position: absolute; left: 40px; top: 27px; display: flex; align-items: center; gap: 7px;
    font-size: 25px; font-weight: 600; color: var(--white); letter-spacing: -0.3px; white-space: nowrap; line-height: 32px; }
  .brand-mark { width: 12px; height: 12px; border-radius: 50%; background: var(--white); }
  .brand-tagline { position: absolute; left: 60px; top: 66px; font-size: 7px; color: var(--white); letter-spacing: 0.4px; white-space: nowrap; }
</style>
</head>
<body>
<main class="cover">
  <section class="headline-panel">
    <h1 class="headline">Singapore’s Latest Property<br>Launches <strong>In One Portal...</strong></h1>
  </section>

  <div class="photo photo-residential" role="img" aria-label="Photo of a residential apartment block under a blue sky"></div>
  <div class="photo photo-commercial" role="img" aria-label="Photo of a modern glass commercial building with lawn"></div>
  <div class="photo photo-tower" role="img" aria-label="Photo of a high-rise condominium tower among greenery"></div>

  <div class="tablet">
    <div class="screen">
      <header class="site-header">
        <div class="site-brand">brightkeyhomes.sg</div>
        <nav class="site-nav"><span>Home</span><span>About Us</span><span>Launches</span><span>Contact</span></nav>
      </header>
      <div class="site-menu"></div>
      <div class="site-hero" role="img" aria-label="Featured project photo banner">
        <div class="hero-title">THE CORALLIS<span>Kenridge Road, D15</span></div>
        <div class="hero-tagline">Waterfront living within your reach</div>
      </div>
      <div class="site-body">
        <article class="listing">
          <div class="listing-image" role="img" aria-label="Project photo"></div>
          <div class="listing-title">Palmrise</div>
          <div class="listing-line">District 15</div>
          <div class="listing-line">Freehold</div>
          <div class="listing-line">420 Units</div>
          <span class="listing-button">View Details</span>
        </article>
        <article class="listing">
          <div class="listing-image" role="img" aria-label="Project photo"></div>
          <div class="listing-title">Harbourlight @ Kenridge</div>
          <div class="listing-line">District 5</div>
          <div class="listing-line">99-yr Lease</div>
          <div class="listing-line">310 Units</div>
          <span class="listing-button">View Details</span>
        </article>
        <aside class="sidebar">
          <div class="sidebar-title">Quick Search</div>
          <div>Property Type</div><div class="field"></div>
          <div>District</div><div class="field"></div>
          <div>Price</div><div class="field"></div>
          <div class="search-button">Search</div>
          <div class="sidebar-title">Subscribe</div>
        </aside>
      </div>
    </div>
  </div>

  <div class="brand-badge">
    <svg viewBox="0 0 334 108" width="334" height="108" aria-hidden="true">
      <polygon points="34,6 334,6 334,102 34,102 4,54" fill="#8dc63f" stroke="#ffffff" stroke-width="4"/>
    </svg>
    <div class="brand-name"><span class="brand-mark"></span>brightkeyhomes.sg</div>
    <div class="brand-tagline">YOUR DAILY SOURCE OF NEW PROPERTY LAUNCHES</div>
  </div>
</main>
</body>
</html>
```